Digital Marketing Website Redesign, modern, fresh, dynamic

Hi there, we would like to freshen up our website and create a new dynamic look. We are a digital marketing agency who specialise in digital transformation in the form of creating websites for appointment bookings. Our clients are service businesses such as hairdressers, dentists and doctors who's patients need to book appointments with them.

Our company name is Tallomex with the point being we can help increase your revenue curve by increasing your appointment bookings.

Our services include building the website, creating campaigns to drive traffic, increasing conversions and monitoring and reporting.

We are playing with a tagline of 'Step into your Digital Transformation' as we have a 5 step journey that customers can take with us getting them from zero to full appointment bookings.

Our current website is www.tallomex-sample.com

You can see a draft design that I mocked up on Canva here https://www.draftboard-sample.com/design/QXB82LmpR7T/KpoW39dnFsYbZet_wqe_OPa/edit?utm_content=QXB82LmpR7T&utm_campaign=designshare&utm_medium=link2&utm_source=sharebutton

Also attached some other homepage ideas. In regard to photos we are open to ideas.

Please let if you need any more information to provide us with an initial design. Thanks million and I look forward to receiving fantastic designs :)

Marian Dobbs
Tallomex

Target Market(s)

Appointment based businesses such as hairdressers, dentists, doctors

Industry/Entity Type

Marketing and Digital

Coding

Coded - Design and coding required

Number of Pages Required

1 page

Colors
0094D4
00A9DD
6FCCEA
C7EBF8
E9F6FB

Requirements
Must have
• Appointment booking CTA
Nice to have
• A website we like https://www.fergalwhitty-sample.ie

```html
<!DOCTYPE html>
<html lang="en">
<head>
<meta charset="utf-8">
<title>Tallomex – Digital Transformation</title>
<link href="https://fonts.googleapis.com/css2?family=Outfit:wght@500;600;700;800&family=Roboto:wght@400;500;700&display=swap" rel="stylesheet">
<style>
:root{
  --blue:#0094D4;
  --blue-bright:#00A9DD;
  --blue-soft:#6FCCEA;
  --blue-pale:#C7EBF8;
  --blue-mist:#EEF8FD;
  --lime:#B5C60C;
  --lime-dark:#9FB007;
  --ink:#111111;
  --text:#555a60;
  --navy:#1f5aa6;
  --footer:#0e0e0e;
  --white:#ffffff;
}
*{box-sizing:border-box;margin:0;padding:0}
html,body{width:1200px;height:4173px;overflow:hidden}
body{position:relative;font-family:'Roboto',sans-serif;color:var(--ink);background:var(--white)}
.abs{position:absolute}
h1,h2,h3,.display{font-family:'Outfit',sans-serif}

/* header */
.topbar{left:0;top:0;width:1200px;height:76px;background:var(--blue)}
.topnav{top:28px;font-size:13px;font-weight:700;color:var(--white);display:flex;gap:14px}
.topnav span.sep{font-weight:400}
.topnav.left{left:110px}
.topnav.right{left:724px}
.btn{display:inline-flex;align-items:center;gap:8px;border-radius:30px;font-weight:700;font-size:14px;color:var(--white);text-transform:uppercase}
.btn-appt{left:906px;top:19px;width:214px;height:38px;background:var(--lime);justify-content:center;text-transform:none;font-size:15px}
.logo-plate{left:0;top:0}
.logo-name{left:470px;top:30px;width:260px;text-align:center;font-family:'Outfit',sans-serif;font-weight:700;font-size:36px;color:var(--navy)}

/* hero */
.hero-photo{left:0;top:76px;width:1200px;height:720px;
  background:
   radial-gradient(ellipse 380px 200px at 780px 430px,rgba(255,255,255,.55),transparent 70%),
   linear-gradient(160deg,rgba(40,60,160,.9) 0%,transparent 40%),
   linear-gradient(15deg,#b0121e 0%,#c8312a 20%,#3a2c8a 45%,#1b2c7a 60%,#0a1c4a 80%,#11102e 100%);}
.hero-panel{left:110px;top:250px;width:620px;height:360px;background:rgba(30,30,30,.62)}
.hero-panel h1{position:absolute;left:49px;top:32px;width:540px;font-size:48px;line-height:56px;font-weight:700;color:var(--white)}
.hero-panel p{position:absolute;left:49px;top:158px;width:520px;font-size:13.5px;line-height:26px;font-weight:500;color:var(--white)}
.btn-start{left:159px;top:518px;width:167px;height:48px;background:var(--blue-bright);justify-content:center;box-shadow:0 4px 10px rgba(0,0,0,.25)}

/* section titles */
.sec-title{left:0;width:1200px;text-align:center;font-size:32px;font-weight:800;text-transform:uppercase}
.sec-sub{left:200px;width:800px;text-align:center;font-size:14.5px;line-height:26px;color:var(--text)}

/* testimonials */
.quote-card{top:1014px;width:312px;height:359px;background:var(--blue-mist);border-radius:34px;padding:22px 22px}
.quote-card .stars{margin-top:14px;display:flex;gap:4px}
.quote-card h3{font-size:22px;line-height:28px;font-weight:500;margin-top:14px}
.quote-card p{font-size:14.5px;line-height:25px;color:var(--text);margin-top:14px}
.reviewer{position:absolute;left:22px;bottom:48px;display:flex;gap:14px;align-items:center}
.avatar{width:50px;height:50px;border-radius:50%;background:radial-gradient(circle at 50% 40%,#c9b7a5,#6c5b52)}
.reviewer strong{display:block;font-size:13px;color:var(--navy);text-transform:uppercase}
.reviewer span{font-size:13.5px;color:var(--text)}

/* routes */
.route-card{top:1523px;width:462px;height:300px;background:var(--white);box-shadow:0 6px 26px rgba(0,0,0,.10);border-radius:4px;padding:26px 30px}
.route-card h3{font-size:21px;line-height:30px;font-weight:600;text-transform:uppercase;width:260px}
.route-card h3 u{text-decoration:none;border-bottom:3px solid var(--lime)}
.tag{position:absolute;right:40px;top:26px;padding:3px 14px;border-radius:14px;background:#f1f3f4;font-size:12.5px;color:#333}
.route-card p{margin-top:20px;font-size:14px;line-height:30px;text-align:justify;color:#333}
.route-card .btn{position:absolute;left:30px;bottom:28px;height:38px;padding:0 20px;background:var(--lime)}

/* services */
.service-band{left:0;top:1870px}
.svc{top:2113px;width:312px}
.svc .shot{height:227px;border-radius:12px}
.svc h3{margin-top:22px;text-align:center;font-size:21px;font-weight:600;color:var(--white)}
.arrow{top:2220px;color:var(--white)}
.btn-signup{left:517px;top:2422px;width:166px;height:48px;background:var(--lime);justify-content:center}

/* team */
.member{top:2833px;width:160px;text-align:center}
.member .ring{width:92px;height:92px;margin:0 auto;border-radius:50%;border:3px solid #e3e3e3;padding:4px}
.member .ring div{width:100%;height:100%;border-radius:50%;background:radial-gradient(circle at 50% 40%,#f2c6a6,#c7794e 70%)}
.member strong{display:block;margin-top:10px;font-size:18px;font-weight:500}
.member span{display:block;margin-top:6px;font-size:14.5px;color:#777}

/* pricing */
.plan{top:3170px;width:284px;height:368px;background:var(--white);box-shadow:0 6px 26px rgba(0,0,0,.10);padding:34px 30px}
.plan h3{font-size:26px;font-weight:500}
.price{margin-top:16px;font-family:'Outfit',sans-serif;font-weight:700;font-size:38px;color:var(--lime)}
.price small{font-family:'Roboto',sans-serif;font-size:14px;color:var(--ink);font-weight:700;margin-left:4px}
.plan ul{list-style:none;margin-top:10px}
.plan li{position:relative;padding-left:28px;margin-bottom:14px;font-size:14px;line-height:25px}
.plan li b{color:var(--blue);font-weight:400;display:block}
.plan li svg{position:absolute;left:0;top:5px}
.plan .btn{position:absolute;left:30px;height:38px;padding:0 30px;background:var(--lime);text-transform:none;font-size:15px}

/* footer */
.footer-shape{left:0;top:3600px}
.f-logo{left:110px;top:3850px;font-family:'Outfit',sans-serif;font-weight:700;font-size:52px;color:var(--navy)}
.f-col{top:3826px;color:var(--white)}
.f-col h4{font-size:17px;font-weight:700;text-transform:uppercase;padding-bottom:6px;display:inline-block;border-bottom:3px solid var(--lime)}
.f-col ul{list-style:none;margin-top:20px}
.f-col li{font-size:12px;margin-bottom:18px;padding-left:6px}
.contact li{display:flex;gap:14px;line-height:20px;margin-bottom:14px}
.contact svg{flex:none;margin-top:3px}
.f-col p{font-size:12px;line-height:20px;margin-top:20px;width:230px;padding-left:6px}
.subscribe-form{margin-top:14px;display:flex;width:252px;height:34px}
.subscribe-form .field{flex:1;background:var(--white);border-radius:17px 0 0 17px;font-size:10px;color:#777;padding:11px 14px}
.subscribe-form .go{width:48px;background:var(--blue);border-radius:0 17px 17px 0;display:flex;align-items:center;justify-content:center}
.socials{display:flex;gap:10px;margin-top:16px;padding-left:6px}
.socials span{width:30px;height:30px;border-radius:50%;background:var(--white)}
.bottom-bar{left:0;top:4112px;width:1200px;height:61px;border-top:1px solid #333;background:var(--footer);color:var(--white);font-size:13px}
.bottom-bar .copy{position:absolute;left:110px;top:23px}
.bottom-bar .legal{position:absolute;left:843px;top:23px;display:flex;gap:12px}
</style>
</head>
<body>

<!-- Header -->
<div class="abs topbar"></div>
<nav class="abs topnav left"><span>Boutique Ecommerce marketing</span><span class="sep">|</span><span>Online booking software</span></nav>
<nav class="abs topnav right"><span>Our Team</span><span class="sep">|</span><span>Contact Us</span></nav>
<a class="abs btn btn-appt">Book an Appointment
  <svg width="14" height="14" viewBox="0 0 14 14" fill="none" stroke="#fff" stroke-width="1.5"><rect x="1" y="2.5" width="12" height="10.5" rx="1"/><path d="M1 6h12M4 1v3M10 1v3"/></svg>
</a>

<!-- Hero -->
<div class="abs hero-photo" role="img" aria-label="Night city road with colourful light streaks rushing toward the skyline"></div>
<svg class="abs logo-plate" width="1200" height="110" viewBox="0 0 1200 110" style="z-index:2"><path d="M470 0H730L688 100H515Z" fill="#fff"/></svg>
<div class="abs logo-name" style="z-index:3">Tallomex</div>

<div class="abs hero-panel">
  <h1>Start your Digital Transformation Journey</h1>
  <p>Digital transformation is a journey. At Tallomex we divide the journey into five key steps that take your business from comprehensive market research to full appointment bookings. Ready to go on that journey?</p>
</div>
<a class="abs btn btn-start">Start here
  <svg width="14" height="14" viewBox="0 0 14 14"><circle cx="7" cy="7" r="7" fill="#fff"/><path d="M5.5 4l3 3-3 3" stroke="#00A9DD" stroke-width="1.8" fill="none"/></svg>
</a>
<svg class="abs" style="left:0;top:700px" width="1200" height="180" viewBox="0 0 1200 180">
  <path d="M0 60C220 0 420 70 640 110C880 150 1060 100 1200 40V180H0Z" fill="var(--lime)"/>
  <path d="M0 80C250 20 450 95 660 125C900 160 1060 150 1200 70V180H0Z" fill="#fff"/>
</svg>

<!-- Testimonials -->
<h2 class="abs sec-title" style="top:945px">Why others choose us?</h2>

<div class="abs quote-card" style="left:110px">
  <svg width="46" height="34" viewBox="0 0 46 34" fill="var(--blue)"><path d="M0 20C0 8 6 2 16 0l2 4C12 6 9 10 9 14h7v20H0Z"/><path d="M26 20C26 8 32 2 42 0l2 4c-6 2-9 6-9 10h7v20H26Z" transform="translate(0 0)"/></svg>
  <div class="stars"><svg width="80" height="13" viewBox="0 0 80 13" fill="var(--lime)"><g id="star"><path d="M6.5 0l2 4.2 4.5.6-3.3 3.1.8 4.5-4-2.2-4 2.2.8-4.5L0 4.8l4.5-.6Z"/></g><use href="#star" x="16.5"/><use href="#star" x="33"/><use href="#star" x="49.5"/><use href="#star" x="66"/></svg></div>
  <h3>100 Bookings in first Month!</h3>
  <p>Tallomex's booking system helped us get over 100 appointment bookings in May 2020.</p>
  <div class="reviewer"><div class="avatar" role="img" aria-label="Portrait of reviewer"></div><div><strong>Lena Harkin</strong><span>Owner, Shear Studio</span></div></div>
</div>

<div class="abs quote-card" style="left:445px">
  <svg width="46" height="34" viewBox="0 0 46 34" fill="var(--blue)"><path d="M0 20C0 8 6 2 16 0l2 4C12 6 9 10 9 14h7v20H0Z"/><path d="M26 20C26 8 32 2 42 0l2 4c-6 2-9 6-9 10h7v20H26Z"/></svg>
  <div class="stars"><svg width="80" height="13" viewBox="0 0 80 13" fill="var(--lime)"><use href="#star"/><use href="#star" x="16.5"/><use href="#star" x="33"/><use href="#star" x="49.5"/><use href="#star" x="66"/></svg></div>
  <h3>From 55 New Patients Per Month!</h3>
  <p>Since Tallomex optimised our marketing campaigns we've had 55-75 new patients per month.</p>
  <div class="reviewer"><div class="avatar" role="img" aria-label="Portrait of reviewer"></div><div><strong>Dr. Amir Sheth</strong><span>Owner, BrightDental</span></div></div>
</div>

<div class="abs quote-card" style="left:777px">
  <svg width="46" height="34" viewBox="0 0 46 34" fill="var(--blue)"><path d="M0 20C0 8 6 2 16 0l2 4C12 6 9 10 9 14h7v20H0Z"/><path d="M26 20C26 8 32 2 42 0l2 4c-6 2-9 6-9 10h7v20H26Z"/></svg>
  <div class="stars"><svg width="80" height="13" viewBox="0 0 80 13" fill="var(--lime)"><use href="#star"/><use href="#star" x="16.5"/><use href="#star" x="33"/><use href="#star" x="49.5"/><use href="#star" x="66"/></svg></div>
  <h3 style="margin-top:22px">25% Increase in Web Traffic!</h3>
  <p>Tallomex have increased our search ranking by 20,000 and our web traffic by 25%</p>
  <div class="reviewer"><div class="avatar" role="img" aria-label="Portrait of reviewer"></div><div><strong>Conor Blaine</strong><span>CEO, LedgerPulse</span></div></div>
</div>

<!-- Routes -->
<h2 class="abs sec-title" style="top:1450px">Choose your route</h2>

<div class="abs route-card" style="left:110px">
  <h3><u>Boutique Ecommerce Marketing</u></h3>
  <span class="tag">#sellonline</span>
  <p>Digital Marketing For Ecommerce Businesses Including Website Development,comprehensive Market Research marketing Campaigns, Content Creation,lead Generation And Sales Pipeline Management</p>
  <a class="btn">Request a quote <svg width="14" height="14" viewBox="0 0 14 14"><circle cx="7" cy="7" r="7" fill="#fff"/><path d="M5.5 4l3 3-3 3" stroke="var(--lime)" stroke-width="1.8" fill="none"/></svg></a>
</div>

<div class="abs route-card" style="left:627px">
  <h3><u>Online Booking Software</u></h3>
  <span class="tag"># appointments</span>
  <p>Easy-to-use Online Booking Syatem For Appointment Based Businesses-social And Map Listings Book Now Intergration -automatic Email Reminders For You And Your Cutomers -marketing Add-ons</p>
  <a class="btn">Book a free trial <svg width="14" height="14" viewBox="0 0 14 14"><circle cx="7" cy="7" r="7" fill="#fff"/><path d="M5.5 4l3 3-3 3" stroke="var(--lime)" stroke-width="1.8" fill="none"/></svg></a>
</div>

<!-- Services -->
<svg class="abs service-band" width="1200" height="760" viewBox="0 0 1200 760">
  <defs><linearGradient id="bandBlue" x1="0" y1="0" x2="0" y2="1"><stop offset="0" stop-color="#0aa3e2"/><stop offset="1" stop-color="#0890d0"/></linearGradient></defs>
  <path d="M0 0C150 40 300 100 460 110C700 120 950 60 1200 20V200H0Z" fill="var(--lime)"/>
  <path d="M0 30C200 90 420 130 640 120C880 110 1050 70 1200 40V650C1050 690 900 700 740 680C500 650 250 620 0 690Z" fill="url(#bandBlue)"/>
  <path d="M0 690C250 620 500 650 740 680C900 700 1050 690 1200 650V740C1100 700 1000 670 880 672C700 676 520 630 300 640C180 646 80 665 0 690Z" fill="var(--lime)"/>
</svg>
<h2 class="abs sec-title" style="top:2043px;color:var(--white)">Our services</h2>
<svg class="abs arrow" style="left:56px" width="14" height="22" viewBox="0 0 14 22"><path d="M11 2L3 11l8 9" stroke="#fff" stroke-width="2.5" fill="none"/></svg>
<svg class="abs arrow" style="left:1128px" width="14" height="22" viewBox="0 0 14 22"><path d="M3 2l8 9-8 9" stroke="#fff" stroke-width="2.5" fill="none"/></svg>

<div class="abs svc" style="left:112px">
  <div class="shot" role="img" aria-label="Team reviewing colourful printed charts on a desk" style="background:linear-gradient(135deg,#d9d2c8,#f4f1ec 55%,#c9b9a6)"></div>
  <h3>A beautiful website</h3>
</div>
<div class="abs svc" style="left:444px">
  <div class="shot" role="img" aria-label="Magnifying glass over printed bar charts" style="background:linear-gradient(135deg,#cfe0f3,#8fb6e0 45%,#e8eef5)"></div>
  <h3>Marketing campaigns</h3>
</div>
<div class="abs svc" style="left:776px">
  <div class="shot" role="img" aria-label="Person using a laptop showing a booking page" style="background:linear-gradient(135deg,#e7dccd,#5d5c66 50%,#2b2d3a)"></div>
  <h3>Review Management</h3>
</div>
<a class="abs btn btn-signup">Sign up <svg width="14" height="14" viewBox="0 0 14 14"><circle cx="7" cy="7" r="7" fill="#fff"/><path d="M5.5 4l3 3-3 3" stroke="var(--lime)" stroke-width="1.8" fill="none"/></svg></a>

<!-- Team -->
<h2 class="abs sec-title" style="top:2692px">Our team</h2>
<p class="abs sec-sub" style="top:2744px">rom business management and web development to creative campaign delivery and social media expertise, our team has all the experience your business needs to it to the top of its digital game.</p>

<div class="abs member" style="left:84px"><div class="ring"><div role="img" aria-label="Team member portrait"></div></div><strong>Declan</strong><span>Account Manager</span></div>
<div class="abs member" style="left:257px"><div class="ring"><div role="img" aria-label="Team member portrait"></div></div><strong>Ronan</strong><span>Account Manager</span></div>
<div class="abs member" style="left:428px"><div class="ring"><div role="img" aria-label="Team member portrait"></div></div><strong>Niamh</strong><span>Website Specia</span></div>
<div class="abs member" style="left:602px"><div class="ring"><div role="img" aria-label="Team member portrait"></div></div><strong>Priya</strong><span>Web developer</span></div>
<div class="abs member" style="left:775px"><div class="ring"><div role="img" aria-label="Team member portrait"></div></div><strong>Marian</strong><span>Content Creator</span></div>
<div class="abs member" style="left:947px"><div class="ring"><div role="img" aria-label="Team member portrait"></div></div><strong>Sofia</strong><span>Social media speciali</span></div>

<!-- Pricing -->
<h2 class="abs sec-title" style="top:3055px">Our pricing</h2>
<p class="abs sec-sub" style="top:3106px">Which plan you take will depend on how many steps you want to take on your digital transformation journey.</p>

<div class="abs plan" style="left:134px">
  <h3>Starter Plan</h3>
  <div class="price">€399<small>/a month</small></div>
  <ul>
    <li><svg width="13" height="13" viewBox="0 0 13 13"><circle cx="6.5" cy="6.5" r="6.5" fill="var(--blue)"/><path d="M3.5 6.7l2 2 4-4" stroke="#fff" stroke-width="1.6" fill="none"/></svg><b>Step 1:</b>Online readiness review based on our 12 point checklist</li>
    <li><svg width="13" height="13" viewBox="0 0 13 13"><circle cx="6.5" cy="6.5" r="6.5" fill="var(--blue)"/><path d="M3.5 6.7l2 2 4-4" stroke="#fff" stroke-width="1.6" fill="none"/></svg><b>Step 2:</b>Implementation</li>
  </ul>
  <a class="btn" style="top:289px">Take 2 steps</a>
</div>

<div class="abs plan" style="left:458px">
  <h3>Premium Plan</h3>
  <div class="price">€599<small>/a month</small></div>
  <ul>
    <li><svg width="13" height="13" viewBox="0 0 13 13"><circle cx="6.5" cy="6.5" r="6.5" fill="var(--blue)"/><path d="M3.5 6.7l2 2 4-4" stroke="#fff" stroke-width="1.6" fill="none"/></svg><b>Step 1:</b>Steps 1, 2 &amp; 3</li>
    <li><svg width="13" height="13" viewBox="0 0 13 13"><circle cx="6.5" cy="6.5" r="6.5" fill="var(--blue)"/><path d="M3.5 6.7l2 2 4-4" stroke="#fff" stroke-width="1.6" fill="none"/></svg><b>Step 3:</b>Content is King</li>
  </ul>
  <a class="btn" style="top:272px">Take 3 steps</a>
</div>

<div class="abs plan" style="left:782px">
  <h3>Ultimate Plan</h3>
  <div class="price">€899<small>/a month</small></div>
  <ul>
    <li style="margin-bottom:8px"><svg width="13" height="13" viewBox="0 0 13 13"><circle cx="6.5" cy="6.5" r="6.5" fill="var(--blue)"/><path d="M3.5 6.7l2 2 4-4" stroke="#fff" stroke-width="1.6" fill="none"/></svg><b>Step 1:</b>Steps 1, 2, 3, 4 &amp; 5</li>
    <li style="margin-bottom:8px"><svg width="13" height="13" viewBox="0 0 13 13"><circle cx="6.5" cy="6.5" r="6.5" fill="var(--blue)"/><path d="M3.5 6.7l2 2 4-4" stroke="#fff" stroke-width="1.6" fill="none"/></svg><b>Step 4:</b>Marketing Campaign</li>
    <li><svg width="13" height="13" viewBox="0 0 13 13"><circle cx="6.5" cy="6.5" r="6.5" fill="var(--blue)"/><path d="M3.5 6.7l2 2 4-4" stroke="#fff" stroke-width="1.6" fill="none"/></svg><b>Step 5:</b>Monitor and Maintain</li>
  </ul>
  <a class="btn" style="top:306px;padding:0 16px">Take the full journey</a>
</div>

<!-- Footer -->
<svg class="abs footer-shape" width="1200" height="573" viewBox="0 0 1200 573">
  <path d="M0 110C200 20 420 10 640 60C860 110 1020 90 1200 30V573H0Z" fill="var(--lime)"/>
  <path d="M0 140C220 60 430 60 640 100C860 140 1030 140 1200 80V573H0Z" fill="var(--footer)"/>
</svg>
<div class="abs f-logo">Tallomex</div>

<div class="abs f-col" style="left:385px">
  <h4>Quick Links</h4>
  <ul><li>5 steps</li><li>Our Pricing</li><li>Ahead of the Curve</li><li>Our Team</li><li>Contact Us</li></ul>
</div>

<div class="abs f-col contact" style="left:580px">
  <h4>Contact Us</h4>
  <ul>
    <li><svg width="12" height="12" viewBox="0 0 12 12" fill="#fff"><path d="M2.5 0L5 3 3.6 4.5c.8 1.6 2.2 3 3.9 3.9L9 7l3 2.5-1.6 2C5.4 11.5.5 6.6.5 1.6Z"/></svg>+353 1 555 0142</li>
    <li style="margin-top:8px"><svg width="12" height="10" viewBox="0 0 12 10"><rect width="12" height="10" rx="1" fill="#fff"/><path d="M0 1l6 4 6-4" stroke="#0e0e0e" fill="none"/></svg>info@tallomex-sample.com</li>
    <li><svg width="10" height="14" viewBox="0 0 10 14" fill="#fff"><path d="M5 0a5 5 0 015 5c0 3.5-5 9-5 9S0 8.5 0 5a5 5 0 015-5zm0 3a2 2 0 100 4 2 2 0 000-4z"/></svg><span style="width:180px">Harbour Enterprise Hub, Quay Road, Westport Business Park, Westport, Co. Mayo Ireland F28 X0X0</span></li>
  </ul>
</div>

<div class="abs f-col" style="left:831px">
  <h4>Subscribe to our blog</h4>
  <p>Sign up today to get resources on how to attract and retain more customers!</p>
  <div class="subscribe-form">
    <div class="field">✉ Email Address</div>
    <div class="go"><svg width="16" height="14" viewBox="0 0 16 14" fill="#fff"><path d="M0 6L16 0 13 14 8 10 6 13V9L13 3 5 8Z"/></svg></div>
  </div>
  <div class="socials"><span></span><span></span><span></span></div>
</div>

<div class="abs bottom-bar">
  <span class="copy">Copyright© 2024 Tallomex | All Rights Reserved</span>
  <span class="legal"><span>Terms and Conditions</span><span>|</span><span>Privacy Policy</span></span>
</div>

</body>
</html>
```